Bright Harbor Web Design & Marketing

Will award a 2nd place prize of $100.00 if someone can come up with a logo to match this design!
Updates

Okay, I'm really looking to see some better designs here. What do you think will bring the best designs out? Please remember with all future submissions I'm looking for a cartoon style / illustrator style website. I'm not sure what the technical term is for it, so I uploaded some images in the brief.

Target Market(s)

Small Business Owners

Industry/Entity Type

Marketing

Logo Text

BrightHarbor.com

Number of Pages Required

1 page

Colors

Designer to choose colors to be used in the design.

Requirements
Must have
• Logo should say BrightHarbor.com I would like more than just a text logo. I want some sort of cool custom graphic / icon with it that will look nice on shirts/hats/etc

```html
<!DOCTYPE html>
<html lang="en">
<head>
<meta charset="utf-8">
<title>Bright Harbor Web Design &amp; Marketing</title>
<link rel="stylesheet" href="https://fonts.googleapis.com/css2?family=Barlow:wght@400;500;600;700;800&display=swap">
<style>
:root{
  --ink:#1b1b1b;
  --white:#ffffff;
  --red:#d8262c;
  --blue:#126f98;
  --yellow:#fcc82e;
  --teal:#2a9cc2;
  --sky:#c4e6f3;
  --muted:#8a8a8a;
  --line:#e7e7e7;
  --paper:#f6f6f6;
  --about:#ececec;
}
*{box-sizing:border-box;margin:0;padding:0}
html,body{width:1200px;height:4813px;overflow:hidden}
body{font-family:"Barlow",Arial,sans-serif;color:var(--ink);background:var(--white);position:relative}
section,header,footer{position:relative;width:1200px;overflow:hidden}
.section-title{position:absolute;left:0;width:100%;text-align:center;font-weight:800;font-size:31px;letter-spacing:.5px;text-transform:uppercase}
.btn{position:absolute;display:flex;align-items:center;justify-content:center;background:var(--red);color:var(--white);font-weight:800;font-size:19px;text-transform:uppercase;border-radius:4px;letter-spacing:.4px}

/* brand mark: name plus one plain circle */
.brand{position:absolute;left:96px;display:flex;align-items:center;gap:9px;font-weight:800;letter-spacing:.3px;white-space:nowrap}
.brand-dot{width:18px;height:18px;border-radius:50%;background:var(--yellow);flex:none}

/* header */
.hero{height:674px;background:linear-gradient(160deg,#2b2b2d 0%,#1c1c1e 45%,#3b3b3e 100%)}
.hero-photo{position:absolute;inset:0;background:radial-gradient(ellipse at 62% 45%,rgba(120,120,125,.45),rgba(0,0,0,0) 55%)}
.hero .brand{top:42px;color:var(--white);font-size:22px}
.nav{position:absolute;top:50px;left:388px;font-weight:700;font-size:12.5px;color:var(--white);text-transform:uppercase}
.nav span{position:absolute;white-space:nowrap}
.nav .active{color:var(--yellow)}
.phone{position:absolute;left:968px;top:47px;display:flex;align-items:center;gap:8px;color:var(--white);font-weight:700;font-size:13px}
.hero-title{position:absolute;left:96px;top:258px;color:var(--white);font-weight:800;font-size:54px;line-height:1.0;text-transform:uppercase}
.hero-sub{position:absolute;left:96px;top:394px;color:var(--white);font-size:17px;font-weight:500}

/* services */
.services-band{height:167px;background:var(--blue)}
.services-band .section-title{top:60px;color:var(--white)}
.services{height:546px;background:var(--white)}
.service-grid{position:absolute;left:96px;top:0;width:1008px;display:grid;grid-template-columns:repeat(3,1fr);grid-template-rows:repeat(3,182px)}
.service{padding:44px 18px 0 18px;border-right:1px solid var(--line);border-bottom:1px solid var(--line)}
.service:nth-child(3n){border-right:none}
.service:nth-child(n+7){border-bottom:none}
.service-head{display:flex;align-items:center;gap:12px;margin-bottom:18px}
.service-name{font-weight:700;font-size:13px;text-transform:uppercase}
.service p{font-size:11.5px;line-height:1.55;color:#a0a0a0}

/* how it works */
.how{height:529px;background:var(--yellow)}
.how .section-title{top:60px;color:var(--white)}
.how-visual{position:absolute;left:411px;top:138px;width:385px;height:337px;border-radius:6px;background:linear-gradient(180deg,#fde7a4 0%,#f3c454 60%,#e6b441 100%)}
.play{position:absolute;left:562px;top:247px}

/* difference */
.difference{height:498px;background:var(--white)}
.difference .section-title{top:70px}
.diff-head{position:absolute;left:173px;top:240px;color:var(--blue);font-weight:800;font-size:20px;text-transform:uppercase}
.diff-text{position:absolute;left:173px;top:274px;width:460px;font-size:15px;line-height:1.55;color:#666}
.dots{position:absolute;left:173px;top:436px;display:flex;gap:10px}
.dots i{width:7px;height:7px;border-radius:50%;background:#cfdde4;display:block}
.dots i:first-child{background:var(--blue)}
.diff-art{position:absolute;left:690px;top:150px}
.rule{position:absolute;left:96px;right:96px;bottom:0;height:1px;background:var(--line)}

/* team */
.team{height:626px;background:var(--white)}
.team .section-title{top:96px}
.member{position:absolute;top:198px;width:262px;text-align:center}
.member .photo{width:192px;height:192px;border-radius:50%;margin:0 auto;background:linear-gradient(160deg,#d9dde2,#9ea6ae)}
.member.lead .photo{border:7px solid var(--yellow)}
.role{margin-top:30px;font-weight:700;font-size:13px;text-transform:uppercase}
.member p{margin:18px auto 0;width:220px;font-size:11.5px;line-height:1.6;color:#9a9a9a}

/* about */
.about{height:613px;background:var(--about)}
.about-photo{position:absolute;left:0;top:0;width:1200px;height:266px;background:linear-gradient(180deg,#dcdcdc 0%,#e9e9e9 100%)}
.about .section-title{top:290px}
.about-text{position:absolute;left:150px;width:900px;text-align:center;font-size:13px;line-height:1.6;color:#3a3a3a}

/* news */
.news{height:648px;background:var(--white)}
.news .section-title{top:62px}
.news-date{position:absolute;left:106px;top:168px;font-weight:800;font-size:16px;text-transform:uppercase}
.news-line{position:absolute;left:106px;top:198px;width:290px;height:1px;background:var(--line)}
.news-head{position:absolute;left:106px;top:228px;width:300px;font-weight:800;font-size:19px;line-height:1.3;text-transform:uppercase}
.news-body{position:absolute;left:106px;top:340px;width:290px;font-size:12.5px;line-height:1.55;color:#8a8a8a}
.arrows{position:absolute;left:106px;top:487px;display:flex;gap:4px}
.arrows span{width:34px;height:24px;border-radius:3px;display:flex;align-items:center;justify-content:center;border:1px solid #d0d0d0;background:var(--white)}
.arrows span.on{background:var(--yellow);border-color:var(--yellow)}
.news-photo{position:absolute;left:449px;top:160px;width:662px;height:353px;border:6px solid #f1f1f1;background:linear-gradient(120deg,#2e5f96 0%,#6f9cc9 45%,#e9eef3 100%)}

/* clients */
.clients{height:386px;background:var(--white)}
.clients .section-title{top:62px}
.client-row{position:absolute;left:96px;width:1008px;display:grid;grid-template-columns:repeat(7,1fr);align-items:center;text-align:center}
.client{font-weight:800;font-size:15px;color:#7c7c7c;text-transform:uppercase;display:flex;align-items:center;justify-content:center;gap:6px}
.client b{width:14px;height:14px;background:#7c7c7c;display:inline-block}

/* footer */
.site-footer{height:126px;background:var(--white);border-top:1px solid var(--line)}
.site-footer .brand{top:54px;color:var(--ink);font-size:20px}
.site-footer .brand-dot{width:16px;height:16px}
.social{position:absolute;left:340px;top:56px;display:flex;gap:8px}
.social i{width:26px;height:26px;border-radius:50%;display:block}
.foot-nav{position:absolute;top:62px;font-weight:700;font-size:12.5px;text-transform:uppercase;white-space:nowrap}
</style>
</head>
<body>

<header class="hero">
  <div class="hero-photo" role="img" aria-label="Photo of a dark desk with a desktop monitor, laptop, tablet and phone showing a web design, with a small plant"></div>
  <div class="brand"><span class="brand-dot"></span>BrightHarbor.com</div>
  <nav class="nav">
    <span class="active" style="left:0">Home</span>
    <span style="left:64px">Services &amp; Pricing</span>
    <span style="left:212px">Our Team</span>
    <span style="left:295px">Clients/Portfolio</span>
    <span style="left:452px">Contact Us</span>
  </nav>
  <div class="phone">
    <svg width="16" height="16" viewBox="0 0 24 24" fill="none" stroke="#fff" stroke-width="2"><path d="M5 3h4l2 5-2.5 1.5a11 11 0 0 0 6 6L16 13l5 2v4a2 2 0 0 1-2 2A16 16 0 0 1 3 5a2 2 0 0 1 2-2z"/></svg>
    1-800-555-0142
  </div>
  <h1 class="hero-title">The Design &amp;<br>Marketing Team</h1>
  <p class="hero-sub">That Always Puts Trust &amp; Loyalty Before Profits</p>
  <div class="btn" style="left:96px;top:449px;width:247px;height:58px">Contact Us Now</div>
</header>

<section class="services-band">
  <h2 class="section-title">What Services Do We Offer?</h2>
</section>

<section class="services">
  <div class="service-grid">
    <div class="service"><div class="service-head"><svg width="22" height="18" viewBox="0 0 22 18" fill="none" stroke="#2a9cc2" stroke-width="1.6"><rect x="1" y="1" width="20" height="13"/><path d="M7 17h8"/></svg><span class="service-name">Website Design &amp; Management</span></div><p>We plan, build and care for fast websites that turn visitors into customers and grow with your business.</p></div>
    <div class="service"><div class="service-head"><svg width="22" height="18" viewBox="0 0 22 18" fill="none" stroke="#2a9cc2" stroke-width="1.6"><rect x="1" y="1" width="20" height="16"/><path d="M5 12l4-5 3 3 4-4"/></svg><span class="service-name">Logo Design &amp; Branding Materials</span></div><p>Custom logos, cards and brand kits that give your company a clear, friendly face people remember and trust.</p></div>
    <div class="service"><div class="service-head"><svg width="22" height="18" viewBox="0 0 22 18" fill="none" stroke="#2a9cc2" stroke-width="1.6"><path d="M1 2h3l2 10h12l2-7H6"/><circle cx="8" cy="16" r="1.3"/><circle cx="16" cy="16" r="1.3"/></svg><span class="service-name">Online Store Design &amp; Management</span></div><p>Online shops that are simple to run, easy to browse and built to take secure orders every day.</p></div>
    <div class="service"><div class="service-head"><svg width="22" height="18" viewBox="0 0 22 18" fill="none" stroke="#2a9cc2" stroke-width="1.6"><path d="M11 17s-6-6-6-10a6 6 0 0 1 12 0c0 4-6 10-6 10z"/><circle cx="11" cy="7" r="2"/></svg><span class="service-name">Local SEO Management</span></div><p>We help customers find you first with listings, reviews and local pages kept accurate and up to date.</p></div>
    <div class="service"><div class="service-head"><svg width="22" height="18" viewBox="0 0 22 18" fill="none" stroke="#2a9cc2" stroke-width="1.6"><circle cx="9" cy="8" r="6"/><path d="M13.5 12.5L20 17"/></svg><span class="service-name">Search Engine Optimization</span></div><p>Careful keyword research, clean code and content work that lift your pages higher in search results each month.</p></div>
    <div class="service"><div class="service-head"><svg width="22" height="18" viewBox="0 0 22 18" fill="none" stroke="#2a9cc2" stroke-width="1.6"><circle cx="5" cy="9" r="2.5"/><circle cx="17" cy="4" r="2.5"/><circle cx="17" cy="14" r="2.5"/><path d="M7 8l8-3M7 10l8 3"/></svg><span class="service-name">Social Media Marketing</span></div><p>Posts, ads and conversations planned around your audience so that every channel brings real attention to your brand.</p></div>
    <div class="service"><div class="service-head"><svg width="22" height="18" viewBox="0 0 22 18" fill="none" stroke="#2a9cc2" stroke-width="1.6"><rect x="5" y="1" width="12" height="5"/><rect x="1" y="6" width="20" height="7"/><rect x="5" y="11" width="12" height="6"/></svg><span class="service-name">Marketing Material &amp; Print Design</span></div><p>Flyers, brochures, banners and signs designed to match your website and printed ready for your next big event.</p></div>
    <div class="service"><div class="service-head"><svg width="22" height="18" viewBox="0 0 22 18" fill="none" stroke="#2a9cc2" stroke-width="1.6"><rect x="1" y="5" width="20" height="12"/><path d="M8 5V2h6v3"/></svg><span class="service-name">Outsourcing Management</span></div><p>Hand us the tasks that slow you down and our team will manage them with care and reporting.</p></div>
    <div class="service"><div class="service-head"><svg width="22" height="18" viewBox="0 0 22 18" fill="none" stroke="#2a9cc2" stroke-width="1.6"><path d="M2 2h18v10H9l-5 4v-4H2z"/></svg><span class="service-name">Consulting</span></div><p>Honest advice on your website, marketing and growth plans, with practical next steps you can act on today.</p></div>
  </div>
</section>

<section class="how">
  <h2 class="section-title">How It Works</h2>
  <div class="how-visual" role="img" aria-label="Flat illustration of two people building a website layout on a large browser window with a play button"></div>
  <svg class="play" width="84" height="84" viewBox="0 0 84 84"><circle cx="42" cy="42" r="40" fill="#126f98"/><path d="M34 27l22 15-22 15z" fill="#fff"/></svg>
</section>

<section class="difference">
  <h2 class="section-title">What Makes Me Different?</h2>
  <h3 class="diff-head">100% Risk Free Investment</h3>
  <p class="diff-text">If we are unable to deliver anything that we say we can we will refund you 100% of your investment.</p>
  <div class="dots"><i></i><i></i><i></i><i></i></div>
  <svg class="diff-art" width="360" height="240" viewBox="0 0 360 240" role="img" aria-label="Two overlapping blue circles with a piggy bank outline icon">
    <circle cx="128" cy="122" r="118" fill="#c4e6f3"/>
    <circle cx="218" cy="96" r="120" fill="#2a9cc2"/>
  </svg>
  <div class="rule"></div>
</section>

<section class="team">
  <h2 class="section-title">My Team</h2>
  <div class="member lead" style="left:81px"><div class="photo" role="img" aria-label="Portrait photo of the chief executive officer"></div><div class="role">Chief Executive Officer</div><p>Leads the company vision, keeps every project on track and makes sure each client feels like family here.</p></div>
  <div class="member" style="left:338px"><div class="photo" role="img" aria-label="Portrait photo of the chief operations officer"></div><div class="role">Chief Operations Officer</div><p>Runs daily operations, schedules our work and keeps communication clear between clients and the design team every day.</p></div>
  <div class="member" style="left:601px"><div class="photo" role="img" aria-label="Portrait photo of the chief technical officer"></div><div class="role">Chief Technical Officer</div><p>Builds and maintains our websites, servers and tools, choosing technology that stays fast, safe and easy to use.</p></div>
  <div class="member" style="left:864px"><div class="photo" role="img" aria-label="Portrait photo of the finance lead"></div><div class="role">Finance</div><p>Handles budgets, billing and planning so our pricing stays fair and every partnership is built to last long.</p></div>
</section>

<section class="about">
  <div class="about-photo" role="img" aria-label="Top-down photo of a white desk with a monitor, keyboard, lamp, glasses, phone, headphones and camera"></div>
  <h2 class="section-title">About Us</h2>
  <p class="about-text" style="top:362px">We believe that honesty and integrity come before personal profits. We are a family owned and operated company. Our parents raised us to take care of each other and that is exactly what we've done. We treat each of our clients with the same loyalty and respect that we give each other.</p>
  <p class="about-text" style="top:426px">We are not looking to have hundreds and thousands of clients. We are looking to expand our family with a handful of like-minded individuals. Companies who take pride in their work and their customers. We want to build mutually beneficial, lucrative, and long-term partnerships.</p>
  <div class="btn" style="left:472px;top:510px;width:256px;height:58px">Contact Us Now</div>
</section>

<section class="news">
  <h2 class="section-title">Featured News</h2>
  <div class="news-date">October 30th 2017</div>
  <div class="news-line"></div>
  <h3 class="news-head">Sed ut perspiciatis unde omnis iste natus error sit voluptatem accusantium</h3>
  <p class="news-body">Doloremque laudantium, totam rem aperiam, eaque ipsa quae ab illo inventore veritatis et quasi architecto beatae vitae dicta sunt explicabo. Nemo enim ipsam voluptatem quia voluptas sit aspernatur aut odit aut fugit, sed quia consequuntur.</p>
  <div class="arrows">
    <span class="on"><svg width="10" height="10" viewBox="0 0 10 10"><path d="M7 1L3 5l4 4" fill="none" stroke="#1b1b1b" stroke-width="1.8"/></svg></span>
    <span><svg width="10" height="10" viewBox="0 0 10 10"><path d="M3 1l4 4-4 4" fill="none" stroke="#1b1b1b" stroke-width="1.8"/></svg></span>
  </div>
  <div class="news-photo" role="img" aria-label="Photo of a man in glasses working at a laptop while holding a phone"></div>
</section>

<section class="clients">
  <h2 class="section-title">Clients</h2>
  <div class="client-row" style="top:162px">
    <div class="client"><b></b>Oakmont</div>
    <div class="client">Rivelle</div>
    <div class="client">Great Pantry</div>
    <div class="client">Northgate</div>
    <div class="client">Harwick</div>
    <div class="client">Silver Crane</div>
    <div class="client">Meadowfield</div>
  </div>
  <div class="client-row" style="top:264px">
    <div class="client">Willow &amp; Stone</div>
    <div class="client">Cobalt Bay</div>
    <div class="client">Ashcroft</div>
    <div class="client">Pembrook Works</div>
    <div class="client">Kelvo</div>
    <div class="client">Aberlin</div>
    <div class="client">Clearflow</div>
  </div>
</section>

<footer class="site-footer">
  <div class="brand"><span class="brand-dot"></span>BrightHarbor.com</div>
  <div class="social" aria-label="Social links">
    <i style="background:#2d9fd9"></i><i style="background:#3b5a9a"></i><i style="background:#d8262c"></i><i style="background:#d8262c"></i>
  </div>
  <span class="foot-nav" style="left:559px">Home</span>
  <span class="foot-nav" style="left:623px">Services &amp; Pricing</span>
  <span class="foot-nav" style="left:771px">Our Team</span>
  <span class="foot-nav" style="left:863px">Clients/Portfolio</span>
  <span class="foot-nav" style="left:1014px">Contact Us</span>
</footer>

</body>
</html>
```